Business Cards Design for the electrical wholesaler: clean bold dynamic :)

We need a business card design that would follow our latest brand guidelines. As an electrical wholesaler we want to bring a fresh look and feel into the industry. The design should be clean bold and dynamic. It should come alive with the renewed energy of our green colour. Our grey colour should keep things balanced and complement the notion of maturity and responsibility. We employ Lato as a corporate font however are not bound by this font and we’re open to interpretation here.

Target Market(s)

Electrical contractors

Industry/Entity Type

Business

Contact Information for Business Card

Logo
Name & Surname: Halyna Dorosh
Job Title: Director of Marketing
Email: halya.dorosh@quillmail.example
Cell phone: XXX.XXX.XXXX
Address: 20517 - 87 Ave. Edmonton, AB, Canada. T6K 4N8
Business Phone: 780.555.0184
Website: www.brovix.example

Font styles to use
Other font styles liked:
• Lato

Requirements
Must have
• Logo & website
Nice to have
• Brand elements - some of them you may find in the attached Brand Guidelines (e.g. three lines on the background signifying "W")

```html
<!DOCTYPE html>
<html lang="en">
<head>
<meta charset="utf-8">
<title>Brovix Business Card</title>
<link href="https://fonts.googleapis.com/css2?family=Lato:wght@400;700;900&display=swap" rel="stylesheet">
<style>
  :root {
    --bg: #3a3b3d;
    --card-dark: #262729;
    --card-band: #4b4e52;
    --green: #84c225;
    --grey-light: #c9cbcd;
    --text-light: #e6e7e8;
    --text-muted: #5c5f63;
  }
  * { margin: 0; padding: 0; box-sizing: border-box; }
  html, body { width: 799px; height: 1200px; overflow: hidden; }
  body {
    background: var(--bg);
    font-family: "Lato", sans-serif;
    position: relative;
  }
  .card {
    position: absolute;
    left: 99px;
    width: 600px;
    height: 343px;
    border-radius: 24px;
    background: var(--card-dark);
    overflow: hidden;
    box-shadow: 0 14px 30px rgba(0,0,0,.45);
  }
  .card--front { top: 128px; }
  .card--back { top: 729px; }

  .brand {
    display: flex;
    align-items: center;
    gap: 14px;
  }
  .brand__mark {
    width: 52px; height: 52px;
    background: var(--green);
    border-radius: 6px;
  }
  .brand__name {
    font-weight: 700;
    color: var(--grey-light);
    line-height: 1;
  }
  .card--front .brand {
    position: absolute;
    left: 50%; top: 50%;
    transform: translate(-50%, -50%);
  }
  .card--front .brand__name { font-size: 76px; }

  .card--back .brand {
    position: absolute;
    left: 34px; top: 22px;
    gap: 10px;
  }
  .card--back .brand__mark { width: 36px; height: 36px; border-radius: 4px; }
  .card--back .brand__name { font-size: 50px; }

  .band {
    position: absolute;
    left: 0; right: 0;
    top: 96px; height: 170px;
    background: var(--card-band);
  }
  .accent-block {
    position: absolute;
    right: 40px; top: 78px;
    width: 150px; height: 206px;
    background: var(--green);
    border-radius: 10px;
  }
  .contact {
    position: absolute;
    left: 34px; top: 112px;
  }
  .contact__name {
    color: var(--green);
    font-weight: 700;
    font-size: 28px;
    line-height: 1.1;
  }
  .contact__title {
    color: var(--text-light);
    font-size: 15px;
    margin-top: 4px;
  }
  .contact__list {
    list-style: none;
    margin-top: 16px;
  }
  .contact__item {
    display: flex;
    align-items: center;
    gap: 8px;
    color: var(--text-light);
    font-size: 15px;
    margin-bottom: 7px;
  }
  .contact__row { display: flex; gap: 18px; }
  .icon { width: 16px; height: 16px; flex: none; }
  .address {
    position: absolute;
    left: 34px; bottom: 30px;
    color: var(--text-muted);
    font-size: 15px;
  }
</style>
</head>
<body>

  <section class="card card--front">
    <div class="brand">
      <span class="brand__mark"></span>
      <span class="brand__name">brovix</span>
    </div>
  </section>

  <section class="card card--back">
    <div class="band"></div>
    <div class="accent-block"></div>

    <div class="brand">
      <span class="brand__mark"></span>
      <span class="brand__name">brovix</span>
    </div>

    <div class="contact">
      <p class="contact__name">Halyna Dorosh</p>
      <p class="contact__title">Founder &amp; CEO</p>
      <ul class="contact__list">
        <li class="contact__item">
          <svg class="icon" viewBox="0 0 16 16"><circle cx="8" cy="8" r="8" fill="#84c225"/><path d="M5.3 4.2h1.5l.7 2-1 .8a5 5 0 0 0 2.5 2.5l.8-1 2 .7v1.5c0 .4-.4.8-.8.8A7.2 7.2 0 0 1 4.5 5c0-.4.4-.8.8-.8z" fill="#262729"/></svg>
          +1 780-555-0184
        </li>
        <li class="contact__row">
          <span class="contact__item">
            <svg class="icon" viewBox="0 0 16 16"><circle cx="8" cy="8" r="8" fill="#84c225"/><rect x="4" y="5" width="8" height="6" rx="1" fill="#262729"/><path d="M4.3 5.4 8 8.3l3.7-2.9" stroke="#84c225" stroke-width="1" fill="none"/></svg>
            hello@brovix.example
          </span>
          <span class="contact__item">
            <svg class="icon" viewBox="0 0 16 16"><circle cx="8" cy="8" r="8" fill="#84c225"/><circle cx="8" cy="8" r="4" fill="none" stroke="#262729" stroke-width="1.2"/><path d="M4 8h8M8 4c-2 2.4-2 5.6 0 8M8 4c2 2.4 2 5.6 0 8" stroke="#262729" stroke-width="1" fill="none"/></svg>
            www.brovix.example
          </span>
        </li>
      </ul>
    </div>

    <p class="address">20517 - 87 Ave. Edmonton, AB, Canada T6K 4N8</p>
  </section>

</body>
</html>
```